Website for a Psychologist in Private Practice

I need a cool web design for my website: www.drkalvoric.com. I would like it to look professional. Keep all the current content and add: Space for video; radio spots (see Silver Cedar Tunes Logo below for those); Quick Inquiry; Friendora link; 5 star rating on Rivo; a map; reviews from former patients. I am open to suggestions.

Target Market(s)

Those seeking individual and marital counseling.

Industry/Entity Type

Mental Health

Number of Pages Required

1 page

Font styles to use
Sans Serif
Other font styles liked:
• I'm open but no hard to read script

Requirements
Must have
• All the content on my home page with link for video and radio spots. List services and degrees and expertices (pics not necessary).
Nice to have
• A video of me and radio conversations (logo of Silver Cedar Tunes radio attached).
Should not have
• Cartoons, comedy, etc.... I don't need pictures of services (marital, depression, etc...) Just list those.

```html
<!DOCTYPE html>
<html lang="en">
<head>
<meta charset="utf-8">
<title>Dr. Marla J. Kalvoric — Psychologist</title>
<link href="https://fonts.googleapis.com/css2?family=Raleway:wght@400;500;600;700;800&family=Lato:wght@400;700&display=swap" rel="stylesheet">
<style>
:root{
  --blue:#2a7fc0;
  --blue-dark:#1f5e92;
  --gold:#c9a64a;
  --gold-bg:#cfbd82;
  --ink:#222;
  --text:#444;
  --light:#f1f1f1;
  --topbar:#3a3a3a;
  --black:#050505;
  --footer:#2a2a2a;
  --copy:#141414;
  --white:#fff;
}
*{box-sizing:border-box;margin:0;padding:0}
html,body{width:1200px;height:3082px;overflow:hidden}
body{font-family:"Lato",Arial,sans-serif;color:var(--text);background:var(--white);position:relative}
.abs{position:absolute}
h2,h3,h4,.nav,.btn{font-family:"Raleway",Arial,sans-serif}
.btn{position:absolute;background:var(--blue);color:var(--white);font-weight:700;font-size:13px;display:flex;align-items:center;justify-content:center;letter-spacing:.5px}
.rule{position:absolute;height:3px;width:40px;background:var(--blue)}

/* top bar */
.topbar{position:absolute;left:0;top:0;width:1200px;height:41px;background:var(--topbar);color:#ddd;font-size:12px}
.topbar .item{position:absolute;top:13px;display:flex;align-items:center;gap:7px}
.topbar .social{position:absolute;top:7px;width:26px;height:26px;background:#4a4a4a}

/* header */
.header{position:absolute;left:0;top:41px;width:1200px;height:95px;background:#ececec}
.logo{position:absolute;left:101px;top:27px;font-family:"Raleway",sans-serif;font-size:32px;font-weight:500;color:var(--gold)}
.nav{position:absolute;top:29px;height:41px;font-size:12px;font-weight:700;color:#2a2a2a;display:flex;align-items:center;white-space:nowrap}
.nav.active{background:var(--blue);color:var(--white);padding:0 16px}

/* hero */
.hero{position:absolute;left:0;top:136px;width:1200px;height:464px;background:linear-gradient(120deg,#cfd3d6 0%,#9ea6ad 45%,#d9dcdd 100%)}
.hero-caption{position:absolute;left:0;bottom:0;width:1200px;height:49px;background:rgba(40,40,40,.55);color:var(--white);font-family:"Lato",sans-serif;font-weight:700;font-size:29px;text-align:center;line-height:49px}
.arrow{position:absolute;top:201px;width:31px;height:29px;background:#222;display:flex;align-items:center;justify-content:center}

/* about */
.about{position:absolute;left:0;top:600px;width:1200px;height:485px;background:var(--light)}
.portrait{position:absolute;left:0;top:0;width:600px;height:485px;background:radial-gradient(circle at 55% 45%,#d8b89a 0%,#8a9a6a 45%,#3f6a32 100%)}
.about h2{position:absolute;left:639px;top:32px;font-size:31px;font-weight:700;color:var(--ink);white-space:nowrap}
.about h2 span{color:var(--gold)}
.about p{position:absolute;left:639px;width:460px;font-size:13.5px;line-height:23px;color:#555}
.about h4{position:absolute;left:639px;top:266px;font-size:15px;color:var(--blue);font-weight:700}
.degrees{position:absolute;left:639px;top:297px;list-style:none;font-size:13px;line-height:23px;color:#555}

/* expertise */
.expertise{position:absolute;left:0;top:1085px;width:1200px;height:695px;background:linear-gradient(135deg,#d6c68f 0%,#c9b77a 50%,#d2c186 100%)}
.expertise h2{position:absolute;left:0;width:1200px;text-align:center;top:34px;font-size:31px;font-weight:700;color:var(--ink)}
.expertise h2 span{color:var(--blue)}
.topic{position:absolute;width:230px}
.topic h3{font-size:16px;font-weight:700;color:var(--blue-dark);margin-bottom:4px}
.topic p{font-size:11.5px;line-height:15px;color:#333}
.topic.right-al{text-align:right}

/* media */
.media{position:absolute;left:0;top:1780px;width:1200px;height:522px;background:var(--black);color:var(--white)}
.media h2{position:absolute;top:60px;font-size:31px;font-weight:700}
.media h2 span{color:var(--blue)}
.quote{position:absolute;left:101px;top:148px;width:470px;font-size:14px;line-height:24px;color:#eee}
.quote .mark{color:var(--gold);font-family:Georgia,serif;font-size:30px;font-weight:700;line-height:10px}
.author{position:absolute;left:101px;top:298px;color:var(--gold);font-weight:700;font-size:15px}
.video{position:absolute;left:614px;top:148px;width:586px;height:306px;background:linear-gradient(90deg,#b9b0a5 0%,#e4e0d8 50%,#a7a39c 100%)}

/* sessions */
.booking{position:absolute;left:99px;top:2339px;width:328px;height:378px;border:6px solid #dedede;background:var(--white)}
.booking h3{position:absolute;left:0;width:100%;text-align:center;top:31px;font-size:16px;font-weight:700;color:var(--blue)}
.field{position:absolute;height:33px;border:1px solid #cfcfcf;font-size:12px;color:#888;padding-left:12px;display:flex;align-items:center}
.field .caret{position:absolute;right:0;top:0;width:30px;height:31px;border-left:1px solid #cfcfcf;display:flex;align-items:center;justify-content:center}
.sessions h2{position:absolute;left:481px;top:2362px;font-size:31px;font-weight:700;color:var(--ink)}
.sessions h2 span{color:var(--blue)}
.session-list{position:absolute;left:481px;top:2440px;width:620px;list-style:none}
.session-list li{position:relative;padding-left:27px;font-size:14px;line-height:20px;color:#333;margin-bottom:13px}
.session-list svg{position:absolute;left:0;top:2px}

/* footer */
.footer{position:absolute;left:0;top:2754px;width:1200px;height:283px;background:var(--footer);color:#ddd}
.footer h4{position:absolute;top:42px;font-size:17px;font-weight:700;color:var(--white)}
.footer h4 span{color:var(--blue)}
.links{position:absolute;left:101px;top:80px;list-style:none;font-size:12.5px;line-height:30px}
.links li::before{content:"•";color:var(--gold);margin-right:8px}
.links li.current{color:var(--gold)}
.contact{position:absolute;left:288px;font-size:12.5px;line-height:18px;display:flex;gap:12px}
.map{position:absolute;left:577px;top:74px;width:282px;height:172px;background:linear-gradient(135deg,#ecebe6,#d9dfe3);border:3px solid #fff}
.follow{position:absolute;top:80px;width:34px;height:34px;border-radius:50%;background:var(--blue)}
.donate{position:absolute;left:939px;top:152px;font-size:12px;font-weight:700;color:var(--white);line-height:15px}
.badge{position:absolute;top:195px;width:78px;height:33px;background:var(--white)}
.copyright{position:absolute;left:0;top:3037px;width:1200px;height:45px;background:var(--copy);color:#ccc;font-size:12.5px;text-align:center;line-height:45px}
</style>
</head>
<body>

<div class="topbar">
  <div class="item" style="left:99px">
    <svg width="14" height="10" viewBox="0 0 14 10"><rect x=".5" y=".5" width="13" height="9" fill="none" stroke="#c9a64a"/><path d="M.5 .5 7 6 13.5 .5" fill="none" stroke="#c9a64a"/></svg>
    mk@drkalvoric.com
  </div>
  <div class="item" style="left:248px">
    <svg width="12" height="12" viewBox="0 0 12 12"><path d="M2 1l2 0 1 3-1.5 1a7 7 0 0 0 3.5 3.5L8 7l3 1v2a1 1 0 0 1-1 1C5 11 1 7 1 2a1 1 0 0 1 1-1z" fill="#c9a64a"/></svg>
    (555) 318 2046
  </div>
  <div class="social" style="left:1050px" aria-label="Friendora"></div>
  <div class="social" style="left:1077px" aria-label="Chirply"></div>
</div>

<header class="header">
  <div class="logo">Dr. Marla J. Kalvoric</div>
  <div class="nav active" style="left:555px">HOME</div>
  <div class="nav" style="left:647px">SESSIONS</div>
  <div class="nav" style="left:736px">MY EXPERTISE</div>
  <div class="nav" style="left:857px">RESOURCES</div>
  <div class="nav" style="left:962px">BIO</div>
  <div class="nav" style="left:1011px">CONTACT US</div>
</header>

<section class="hero" role="img" aria-label="Photo of a couple in a counseling session with a therapist">
  <div class="arrow" style="left:6px"><svg width="10" height="12"><path d="M8 1 2 6l6 5" fill="none" stroke="#fff" stroke-width="2"/></svg></div>
  <div class="arrow" style="left:1160px"><svg width="10" height="12"><path d="M2 1l6 5-6 5" fill="none" stroke="#fff" stroke-width="2"/></svg></div>
  <div class="hero-caption">I am a psychologist providing individual and marital counseling</div>
</section>

<section class="about">
  <div class="portrait" role="img" aria-label="Portrait of Dr. Marla J. Kalvoric outdoors"></div>
  <h2>ABOUT <span>DR. MARLA J. KALVORIC</span></h2>
  <div class="rule" style="left:639px;top:88px"></div>
  <p style="top:110px">While I acknowledge the importance of my education, I also appreciate the role my experiences have played in allowing me to relate so well to others. Allow me to share those I feel are most relevant with you.</p>
  <p style="top:185px">I survived an abusive childhood that my mother and sister unfortunately did not.&nbsp; And it was my grief and desire to become stronger than my past that led me to counseling. A process that clearly changed my life</p>
  <h4>MY DEGREES</h4>
  <ul class="degrees">
    <li>Doctoral Degree in Clinical Psychology</li>
    <li>Masters Degree in Counseling Psychology</li>
    <li>Doctoral Internship, Coastal University Medical Center</li>
    <li>Masters Internship, Brookfield Clinic</li>
  </ul>
  <div class="btn" style="left:639px;top:409px;width:113px;height:41px">READ MORE</div>
</section>

<section class="expertise">
  <h2>MY <span>EXPERTISE</span></h2>
  <div class="rule" style="left:580px;top:86px"></div>
  <svg class="abs" style="left:0;top:0" width="1200" height="695" viewBox="0 0 1200 695">
    <g stroke="#8aa6b8" stroke-width="1.5" fill="none">
      <line x1="567" y1="374" x2="567" y2="197"/><line x1="567" y1="374" x2="707" y2="275"/>
      <line x1="567" y1="374" x2="707" y2="477"/><line x1="567" y1="374" x2="567" y2="575"/>
      <line x1="567" y1="374" x2="429" y2="477"/><line x1="567" y1="374" x2="429" y2="275"/>
      <polyline points="420,144 500,144 520,160"/>
      <polyline points="272,270 370,270"/>
      <polyline points="765,265 870,265"/>
      <polyline points="282,492 370,490"/>
      <polyline points="765,460 800,450 876,450"/>
      <polyline points="620,618 660,614 735,614"/>
    </g>
    <g fill="#2a7fc0"><circle cx="272" cy="270" r="3"/><circle cx="870" cy="265" r="3"/><circle cx="282" cy="492" r="3"/><circle cx="876" cy="450" r="3"/></g>
    <defs><radialGradient id="goldFill" cx="50%" cy="40%"><stop offset="0" stop-color="#d9b95c"/><stop offset="1" stop-color="#a8872f"/></radialGradient></defs>
    <g fill="url(#goldFill)" stroke="#fff" stroke-width="7">
      <circle cx="567" cy="197" r="52"/><circle cx="707" cy="275" r="52"/><circle cx="707" cy="477" r="52"/>
      <circle cx="567" cy="575" r="52"/><circle cx="429" cy="477" r="52"/><circle cx="429" cy="275" r="52"/>
    </g>

    <!-- Dating: heart -->
    <path class="icon-dating" d="M567 219 C545 203 540 193 540 185 C540 176 547 170 555 170 C561 170 565 174 567 178 C569 174 573 170 579 170 C587 170 594 176 594 185 C594 193 589 203 567 219Z" fill="#fff"/>
    <path d="M559 190h16M567 182v16" stroke="#b89640" stroke-width="3" fill="none"/>

    <!-- Marriage: two people -->
    <g class="icon-marriage" fill="#fff">
      <circle cx="696" cy="255" r="7"/><rect x="688" y="265" width="16" height="22" rx="4"/><rect x="690" y="285" width="5" height="15"/><rect x="697" y="285" width="5" height="15"/>
      <circle cx="718" cy="255" r="7"/><path d="M710 265h16l4 24h-24z"/><rect x="713" y="288" width="4" height="12"/><rect x="719" y="288" width="4" height="12"/>
    </g>

    <!-- Parenting & professional: joined hands -->
    <g class="icon-partnership" fill="none" stroke="#fff" stroke-width="5" stroke-linecap="round" stroke-linejoin="round">
      <path d="M680 470l14-8 14 10 10-6 16 10"/>
      <path d="M690 480l12 10 8-6 8 6 10-8"/>
      <path d="M676 466l-4 4M738 472l4 4"/>
    </g>

    <!-- Depression & anxiety: rain cloud -->
    <g class="icon-mood" fill="#fff">
      <path d="M548 577a10 10 0 0 1 3-19 14 14 0 0 1 26-4 10 10 0 0 1 13 10 8 8 0 0 1-2 13z"/>
      <path d="M553 584l-3 8M564 584l-3 8M575 584l-3 8M586 584l-3 8" stroke="#fff" stroke-width="3" stroke-linecap="round"/>
    </g>

    <!-- Personality disorders: pair with exchange arrows -->
    <g class="icon-personality" fill="#fff">
      <circle cx="417" cy="466" r="7"/><rect x="408" y="476" width="18" height="18" rx="5"/>
      <circle cx="441" cy="466" r="7"/><rect x="432" y="476" width="18" height="18" rx="5"/>
      <path d="M420 502h18l-4-4M438 502l-4 4" fill="none" stroke="#fff" stroke-width="2.5" stroke-linecap="round"/>
    </g>

    <!-- Life management: checklist -->
    <g class="icon-life">
      <rect x="412" y="252" width="34" height="44" rx="3" fill="#fff"/>
      <rect x="421" y="247" width="16" height="9" rx="2" fill="#fff" stroke="#b89640" stroke-width="2"/>
      <path d="M418 265l3 3 5-5M418 277l3 3 5-5M418 289l3 3 5-5" fill="none" stroke="#b89640" stroke-width="2"/>
      <path d="M430 266h10M430 278h10M430 290h10" stroke="#b89640" stroke-width="2"/>
    </g>

    <circle cx="567" cy="374" r="68" fill="#2a6fa8" stroke="#fff" stroke-width="8"/>
    <text x="567" y="366" text-anchor="middle" font-family="Raleway, sans-serif" font-size="17" font-weight="600" fill="#d8c27a">Dr. Marla J.</text>
    <text x="567" y="390" text-anchor="middle" font-family="Raleway, sans-serif" font-size="17" font-weight="600" fill="#d8c27a">Kalvoric</text>
  </svg>
  <div class="topic right-al" style="left:180px;top:130px"><h3>Dating</h3><p>Lorem ipsum dolor sit amensectetuer<br>adipiscing elit, seddiam no</p></div>
  <div class="topic right-al" style="left:33px;top:260px"><h3>Life Management</h3><p>Lorem ipsum dolor sit<br>amensectetuer adipiscing elit,</p></div>
  <div class="topic" style="left:875px;top:255px"><h3>Marriage</h3><p>Lorem ipsum dolor sit amensectetuer<br>adipiscing elit, seddiam no</p></div>
  <div class="topic right-al" style="left:47px;top:481px"><h3>Personality Disorders</h3><p>Lorem ipsum dolor sit<br>amensectetuer adipiscing elit,</p></div>
  <div class="topic" style="left:882px;top:442px;width:240px"><h3>Parenting &amp; Professional<br>Relationships</h3><p>Lorem ipsum dolor sit amensectetuer<br>adipiscing elit, seddiam no</p></div>
  <div class="topic" style="left:742px;top:594px;width:260px"><h3>Depression &amp; Anxiety Issues</h3><p>Lorem ipsum dolor sit amensectetuer<br>adipiscing elit, seddiam no</p></div>
</section>

<section class="media">
  <h2 style="left:101px">RADIO <span>CONVERSATIONS</span></h2>
  <div class="rule" style="left:101px;top:110px"></div>
  <p class="quote"><span class="mark">“</span> Lorem ipsum dolor sit amet, consectetuer adipiscing elit, sed diam nonummy tincidunt ut laoreet dolore magna quam erat volutpat. Ut wisi enim ad minim veniam, quis nostrud exerci tation ullamcorper suscipit lobortis nisl ut aliquip ex ea commodo consequat. Duis autem vel eum iriure.laoreet dolore magna quam erat <span class="mark">”</span></p>
  <div class="author">Evan Mercer</div>
  <div class="btn" style="left:101px;top:386px;width:109px;height:39px">VIEW ALL</div>
  <h2 style="left:614px">VIEW <span>VIDEO</span></h2>
  <div class="rule" style="left:614px;top:110px"></div>
  <div class="video" role="img" aria-label="Video still of a family counseling session">
    <svg class="abs" style="left:244px;top:103px" width="60" height="60" viewBox="0 0 60 60"><circle cx="30" cy="30" r="27" fill="rgba(0,0,0,.25)" stroke="#fff" stroke-width="3"/><path d="M23 17v26l21-13z" fill="#fff"/></svg>
  </div>
</section>

<section class="sessions">
  <div class="booking">
    <h3>SCHEDULE AN APPOINTMENT</h3>
    <div class="field" style="left:29px;top:90px;width:258px">Full Name</div>
    <div class="field" style="left:29px;top:141px;width:258px">Phone Number</div>
    <div class="field" style="left:29px;top:191px;width:122px">Date<span class="caret"><svg width="8" height="5"><path d="M0 0h8L4 5z" fill="#c9a64a"/></svg></span></div>
    <div class="field" style="left:165px;top:191px;width:122px">Time<span class="caret"><svg width="8" height="5"><path d="M0 0h8L4 5z" fill="#c9a64a"/></svg></span></div>
    <div class="field" style="left:29px;top:242px;width:258px">Location<span class="caret"><svg width="8" height="5"><path d="M0 0h8L4 5z" fill="#c9a64a"/></svg></span></div>
    <div class="btn" style="left:111px;top:294px;width:94px;height:37px">SUBMIT</div>
  </div>
  <h2>MY <span>SESSIONS</span></h2>
  <div class="rule" style="left:481px;top:2416px"></div>
  <ul class="session-list">
    <li><svg width="16" height="14"><path d="M1 7l5 5L15 1" fill="none" stroke="#2a7fc0" stroke-width="2.5"/></svg>Individual sessions are 50 minutes in length</li>
    <li><svg width="16" height="14"><path d="M1 7l5 5L15 1" fill="none" stroke="#2a7fc0" stroke-width="2.5"/></svg>Marriage sessions are typically 50 to 75 minutes in length</li>
    <li><svg width="16" height="14"><path d="M1 7l5 5L15 1" fill="none" stroke="#2a7fc0" stroke-width="2.5"/></svg>Family sessions are 60 to 75 minutes in length</li>
    <li><svg width="16" height="14"><path d="M1 7l5 5L15 1" fill="none" stroke="#2a7fc0" stroke-width="2.5"/></svg>Divorce Mediation sessions are primarily conducted with individual sessions for each spouse with meetings as a couple kept to a minimum</li>
    <li><svg width="16" height="14"><path d="M1 7l5 5L15 1" fill="none" stroke="#2a7fc0" stroke-width="2.5"/></svg>Custody Evaluation sessions are usually initiated by each parties attorneys or the presiding judge</li>
    <li><svg width="16" height="14"><path d="M1 7l5 5L15 1" fill="none" stroke="#2a7fc0" stroke-width="2.5"/></svg>Testing sessions vary in length dependent upon the nature of the psychological assessment needed</li>
  </ul>
</section>

<footer class="footer">
  <h4 style="left:101px">Quick <span>Links</span></h4>
  <ul class="links">
    <li class="current">Home</li><li>Sessions</li><li>My Expertise</li><li>Resources</li><li>Bio</li><li>Contact Us</li>
  </ul>
  <h4 style="left:288px">Contact <span>Details</span></h4>
  <div class="contact" style="top:80px">
    <svg width="12" height="16" viewBox="0 0 12 16"><path d="M6 0a6 6 0 0 1 6 6c0 4-6 10-6 10S0 10 0 6a6 6 0 0 1 6-6z" fill="#ddd"/><circle cx="6" cy="6" r="2.2" fill="#2a2a2a"/></svg>
    <div><b style="color:#fff">Dr. Marla J. Kalvoric</b><br>418 Linden Court #210<br>Harbor Vale, CA 90410</div>
  </div>
  <div class="contact" style="top:148px"><svg width="12" height="12" viewBox="0 0 12 12"><path d="M2 1l2 0 1 3-1.5 1a7 7 0 0 0 3.5 3.5L8 7l3 1v2a1 1 0 0 1-1 1C5 11 1 7 1 2a1 1 0 0 1 1-1z" fill="#ddd"/></svg>(555) 318 2046</div>
  <div class="contact" style="top:187px"><svg width="10" height="14" viewBox="0 0 10 14"><rect x="1" y="0" width="8" height="14" rx="1.5" fill="#ddd"/><rect x="2.5" y="2" width="5" height="8" fill="#2a2a2a"/></svg>(555) 318 2046</div>
  <div class="contact" style="top:226px"><svg width="13" height="10" viewBox="0 0 14 10"><rect x=".5" y=".5" width="13" height="9" fill="none" stroke="#ddd"/><path d="M.5 .5 7 6 13.5 .5" fill="none" stroke="#ddd"/></svg>mk@drkalvoric.com</div>
  <h4 style="left:577px">Location <span>Map</span></h4>
  <div class="map" role="img" aria-label="Street map showing the office location"></div>
  <h4 style="left:939px">Follow <span>Us</span></h4>
  <div class="follow" style="left:938px;background:#3b5a9a" aria-label="Friendora"></div>
  <div class="follow" style="left:986px;background:#2a9fe0" aria-label="Chirply"></div>
  <div class="donate">A portion of all revenue<br>is donated to</div>
  <div class="badge" style="left:939px" aria-label="Partner charity"></div>
  <div class="badge" style="left:1023px" aria-label="Partner charity"></div>
</footer>
<div class="copyright">Copyright © 2016 Dr. Marla J. Kalvoric. All Rights Reserved</div>

</body>
</html>
```